CBD/HEMP website for e-commerce store

I need a CBD website for my shopify store. I am looking for a layout similar to these site ( https://quietmeadowcbd.com/ ) (https://elmridgecbd.com/) but with my logo and products. I am attaching what my logo looks like so that it helps with the design.

Target Market(s)

CBD HEMP CANNABIS

Industry/Entity Type

Cannabis

Coding

Coded - Design and coding required

Number of Pages Required

5+ page

Requirements
Nice to have
• I would like for it to have a trendy/galaxy feel

```html
<!DOCTYPE html>
<html lang="en">
<head>
<meta charset="utf-8">
<title>Lumivo – CBD Store</title>
<link rel="stylesheet" href="https://fonts.googleapis.com/css2?family=Oswald:wght@400;500&family=Roboto:ital,wght@0,400;0,500;0,700;1,400&display=swap">
<style>
:root{
  --green:#3d9a1f;
  --green-soft:#6ab95a;
  --ink:#1d1d1d;
  --muted:#6d6d6d;
  --night:#1a1330;
  --night-2:#2b1b46;
  --plum:#5b1a4e;
  --footer:#150f24;
  --line:#e4e4e4;
  --star:#f5a623;
  --grey-bg:#f3f3f3;
}
*{box-sizing:border-box;margin:0;padding:0}
html,body{width:1200px;height:5055px;overflow:hidden}
body{position:relative;font-family:'Roboto',sans-serif;color:var(--ink);background:#fff}
.abs{position:absolute}
.btn{position:absolute;background:var(--green);color:#fff;font:500 14px 'Roboto',sans-serif;text-transform:uppercase;display:flex;align-items:center;justify-content:center;letter-spacing:.3px}

/* hero */
.hero{left:0;top:0;width:1200px;height:634px;background:radial-gradient(ellipse at 75% 40%,#4a2a6e 0%,var(--night-2) 40%,var(--night) 80%)}
.topbar{left:0;top:0;width:1200px;height:43px;color:#fff;font-size:13px}
.topbar .mail{left:100px;top:12px}
.topbar .acct{left:868px;top:10px;font-size:11px}
.topbar .cart{left:1037px;top:13px;font-size:11px}
.brand{left:110px;top:60px;color:#fff;font:500 30px 'Roboto',sans-serif;letter-spacing:2px;display:flex;align-items:center;gap:10px}
.brand i{width:16px;height:16px;border-radius:50%;background:var(--green);display:block}
.nav{left:380px;top:73px;display:flex;gap:32px;color:#fff;font-size:13px}
.hero-title{left:98px;top:250px;font:400 58px/70px 'Oswald',sans-serif;color:#fff;letter-spacing:.5px;white-space:nowrap}
.hero-sub{left:100px;top:334px;font:500 24px/36px 'Roboto',sans-serif;color:#fff;text-transform:uppercase;white-space:nowrap}
.arrow-c{width:44px;height:44px;border:1.5px solid #ccc;border-radius:50%}
.hero-frame{left:793px;top:208px;width:248px;height:263px;border:3px solid var(--green)}
.hero-bud{left:830px;top:238px;width:170px;height:290px;border-radius:45% 45% 40% 40%;background:radial-gradient(circle at 40% 40%,#b3a86b,#6f7a3a 60%,#3f4a1f)}
.seal{left:730px;top:415px;width:90px;height:90px;border-radius:50%;background:#fff;border:4px double #222}

/* categories */
.cat{top:648px;width:379px;height:498px}
.cat .lbl{position:absolute;left:28px;top:360px;color:#fff}
.cat small{font:500 13px 'Roboto',sans-serif}
.cat h3{font:500 36px 'Roboto',sans-serif;margin-top:2px}
.cat .btn{left:28px;top:432px;width:120px;height:38px;font-size:12px}

/* section heading */
.leaf{width:40px;height:56px}
.heading{left:0;width:1200px;text-align:center;font:700 38px 'Roboto',sans-serif;text-transform:uppercase}
.heading span{color:var(--green)}

/* product cards */
.card{width:242px;height:336px;border:1px solid var(--line);background:#fff;text-align:center}
.card .ph{position:absolute;left:30px;top:20px;width:180px;height:190px;border-radius:45%}
.card .new{position:absolute;left:4px;top:4px;width:70px;height:50px;background:linear-gradient(135deg,var(--green) 50%,transparent 50%)}
.card .new b{position:absolute;left:8px;top:12px;color:#fff;font:500 10px 'Roboto',sans-serif;transform:rotate(-40deg)}
.card .stars{position:absolute;left:0;width:100%;top:228px;color:var(--star);font-size:19px;letter-spacing:1px}
.card .name{position:absolute;left:0;width:100%;top:258px;font-size:15px}
.card .price{position:absolute;left:0;width:100%;top:296px;font:500 16px 'Roboto',sans-serif;color:var(--green)}
.card.active{background:var(--green-soft);border:6px solid #fff;outline:1px solid var(--line)}
.card.active .stars,.card.active .name{color:#fff}
.slide-dot{width:26px;height:34px;border-radius:50%;background:#ccc}

/* quality */
.quality-art{left:250px;top:1716px;width:220px;height:250px;border-radius:50%;background:radial-gradient(closest-side,#8cc63f,#3d8a1f 70%,rgba(61,138,31,0))}
.q-title{left:0;width:1200px;top:1880px;text-align:center;font:400 78px/90px 'Oswald',sans-serif;color:var(--green)}
.q-sub{left:0;width:1200px;top:1970px;text-align:center;font:500 30px 'Roboto',sans-serif}
.q-text{left:250px;width:700px;top:2024px;text-align:center;font-size:16px;line-height:27px;color:#444}

.tab{top:2375px;height:47px;font:500 15px 'Roboto',sans-serif;display:flex;align-items:center;justify-content:center}

/* benefits */
.benefits{left:0;top:2952px;width:1200px;height:582px;background:radial-gradient(ellipse at 50% 50%,#3a3560,#1c1a34 70%)}
.ben{width:330px;color:#fff}
.ben h4{font:500 14px 'Roboto',sans-serif;text-transform:uppercase;margin-bottom:5px}
.ben p{font-size:11px;line-height:18px;color:#ddd}
.ben.l{text-align:right}
.ico{width:46px;height:46px}
.plant{left:420px;top:3140px;width:360px;height:380px;border-radius:50%;background:radial-gradient(closest-side,#9bc85a,#4b8a2a 70%,rgba(75,138,42,0))}

/* blog */
.post{top:3741px;width:326px}
.post .ph{height:207px}
.post h5{margin-top:26px;font:500 16px/22px 'Roboto',sans-serif}
.post p{margin-top:8px;font-size:11px;line-height:19px;color:var(--muted)}
.post a{display:block;margin-top:12px;font:500 11px 'Roboto',sans-serif;color:var(--green);text-decoration:none}

/* testimonials */
.testi{left:0;top:4200px;width:1200px;height:494px;background:var(--grey-bg)}
.tcard{top:4399px;width:428px;height:185px;background:#fff}
.tcard p{position:absolute;left:42px;top:22px;width:370px;font:italic 13.5px/26px 'Roboto',sans-serif;color:#333}
.tcard b{position:absolute;left:42px;top:142px;font:500 15px 'Roboto',sans-serif}
.quote{left:-28px;top:56px;width:60px;height:60px;border-radius:50%;background:var(--green);border:5px solid var(--grey-bg);color:#fff;font:700 44px/56px 'Roboto',sans-serif;text-align:center}
.dot{top:4615px;width:9px;height:9px;border-radius:50%;background:#ccc}

/* newsletter */
.news{left:0;top:4694px;width:1200px;height:106px;background:var(--plum);color:#fff}
.news .txt{left:182px;top:31px;font-size:15px;line-height:22px}
.news input{position:absolute;left:614px;top:30px;width:318px;height:48px;border:none;padding:0 14px;font:13px 'Roboto',sans-serif}
.news .btn{left:946px;top:30px;width:150px;height:48px;font-weight:700}

/* footer */
.footer{left:0;top:4800px;width:1200px;height:255px;background:radial-gradient(ellipse at 50% 30%,#2a1e44,var(--footer) 70%);color:#fff}
.fcol h6{font:500 16px 'Roboto',sans-serif;margin-bottom:16px}
.fcol h6 span{color:var(--green)}
.fcol ul{list-style:none;font-size:11px;line-height:20px}
.soc{width:34px;height:34px;border:1.5px solid #fff;border-radius:50%}
.copy{left:0;width:1200px;top:5012px;text-align:center;font-size:11px;color:#ccc}
</style>
</head>
<body>

<!-- Hero -->
<div class="abs hero" role="img" aria-label="Dark purple galaxy background with cannabis leaves"></div>
<div class="abs topbar">
  <div class="abs mail">✈ info@lumivo.com</div>
  <div class="abs acct">◯ MY ACCOUNT &nbsp;&nbsp;&nbsp;&nbsp;&nbsp; <svg width="22" height="22" viewBox="0 0 22 22" style="vertical-align:middle"><circle cx="9" cy="9" r="7" fill="none" stroke="#fff" stroke-width="1.6"/><line x1="14" y1="14" x2="20" y2="20" stroke="#fff" stroke-width="1.6"/></svg></div>
  <div class="abs cart">CART 🛒</div>
</div>
<div class="abs brand"><i></i>LUMIVO</div>
<nav class="abs nav"><span>HOME</span><span>CANNABIS</span><span>CONCENTRATES</span><span>SHOP</span><span>HOW TO ORDER</span><span>FAQ'S</span><span>ABOUT US</span><span>PROMOS</span></nav>
<h1 class="abs hero-title">BUY MY CBD ONLINE</h1>
<div class="abs hero-sub">World's best cannabis delivered<br>straight to your doorsteps</div>
<div class="btn" style="left:100px;top:432px;width:182px;height:43px">Shopping Now</div>
<div class="abs arrow-c" style="left:33px;top:348px"></div>
<div class="abs arrow-c" style="left:1122px;top:348px"></div>
<div class="abs hero-frame"></div>
<div class="abs hero-bud" role="img" aria-label="Cannabis flower bud"></div>
<div class="abs seal" role="img" aria-label="Satisfaction guarantee seal"></div>

<!-- Categories -->
<div class="abs cat" style="left:18px;background:linear-gradient(160deg,#5e6e4c,#2f3a25 60%,#1e241a)" role="img" aria-label="Cannabis plant close-up">
  <div class="lbl"><small>CBD</small><h3>Flowers</h3></div><div class="btn">Shop Now</div></div>
<div class="abs cat" style="left:412px;background:linear-gradient(160deg,#c9c4bd,#8a5a55 55%,#4a1e2a)" role="img" aria-label="Woman smoking a pre-roll">
  <div class="lbl"><small>CBD</small><h3 style="font-family:'Oswald',sans-serif;font-weight:400">Pre-Rolls</h3></div><div class="btn">Shop Now</div></div>
<div class="abs cat" style="left:805px;background:linear-gradient(160deg,#9aa48a,#b07a5a 50%,#6b4a36)" role="img" aria-label="Woman holding a vape pen">
  <div class="lbl"><small>CBD</small><h3>Vapes</h3></div><div class="btn">Shop Now</div></div>

<!-- Featured products 1 -->
<svg class="abs leaf" style="left:580px;top:1236px" viewBox="0 0 40 56"><path d="M20 2 C24 14 24 26 20 40 C16 26 16 14 20 2Z M20 40 C10 34 4 26 2 18 C10 22 16 30 20 40Z M20 40 C30 34 36 26 38 18 C30 22 24 30 20 40Z" fill="var(--green)"/><line x1="20" y1="40" x2="20" y2="54" stroke="var(--green)" stroke-width="2"/></svg>
<div class="abs heading" style="top:1303px"><span>Featured</span> Products</div>
<div class="abs slide-dot" style="left:67px;top:1538px"></div>
<div class="abs slide-dot" style="left:1107px;top:1538px;background:#8cd47a"></div>

<div class="abs card" style="left:88px;top:1386px"><div class="ph" style="background:radial-gradient(circle,#a3a86a,#6d7a3a 60%,transparent 70%)" role="img" aria-label="Cannabis bud"></div><div class="new"><b>NEW</b></div><div class="stars">★★★★★</div><div class="name">Mango Dusk</div><div class="price">$27.00 &nbsp;|&nbsp; $180.00</div></div>
<div class="abs card active" style="left:349px;top:1386px"><div class="ph" style="background:radial-gradient(circle,#4aa84a,#2f8a2f 60%,transparent 70%)" role="img" aria-label="Cannabis bud"></div><div class="stars">★★★★★</div><div class="name">Mango Dusk</div><div class="btn" style="left:42px;top:288px;width:140px;height:32px;background:#fff;color:var(--green);font-size:12px">🛒 &nbsp;Add to Card</div></div>
<div class="abs card" style="left:610px;top:1386px"><div class="ph" style="background:radial-gradient(circle,#b9b98c,#6f8350 60%,transparent 70%)" role="img" aria-label="Cannabis bud"></div><div class="new"><b>NEW</b></div><div class="stars">★★★★★</div><div class="name">Mango Dusk</div><div class="price">$27.00 &nbsp;|&nbsp; $180.00</div></div>
<div class="abs card" style="left:870px;top:1386px"><div class="ph" style="background:radial-gradient(circle,#b5a86a,#6b7a40 60%,transparent 70%)" role="img" aria-label="Cannabis bud"></div><div class="new"><b>NEW</b></div><div class="stars">★★★★★</div><div class="name">Mango Dusk</div><div class="price">$27.00 &nbsp;|&nbsp; $180.00</div></div>

<!-- Highest quality -->
<div class="abs quality-art" role="img" aria-label="Cannabis leaf with oil dropper"></div>
<div class="abs q-title">HIGHEST QUALITY</div>
<div class="abs q-sub">WORLD'S BEST MEDICAL MARIJUANA</div>
<div class="abs q-text">Lorem ipsum dolor sit amet, consectetur adipiscing elit, sed do eiusmod tempor incididunt ut labore et dolore magna aliqua. Quis ipsum suspendisse</div>
<div class="btn" style="left:500px;top:2100px;width:200px;height:46px">Browse Products</div>

<!-- Featured products 2 -->
<svg class="abs leaf" style="left:580px;top:2236px" viewBox="0 0 40 56"><path d="M20 2 C24 14 24 26 20 40 C16 26 16 14 20 2Z M20 40 C10 34 4 26 2 18 C10 22 16 30 20 40Z M20 40 C30 34 36 26 38 18 C30 22 24 30 20 40Z" fill="var(--green)"/><line x1="20" y1="40" x2="20" y2="54" stroke="var(--green)" stroke-width="2"/></svg>
<div class="abs heading" style="top:2303px"><span>Featured</span> Products</div>
<div class="abs tab" style="left:424px;width:168px;background:var(--green);color:#fff">NEW ARRIVALS</div>
<div class="abs tab" style="left:606px;width:170px;border:1px solid var(--line);color:var(--green)">BEST - SELLING</div>
<div class="abs slide-dot" style="left:67px;top:2606px"></div>
<div class="abs slide-dot" style="left:1107px;top:2606px;background:#8cd47a"></div>

<div class="abs card" style="left:88px;top:2456px"><div class="ph" style="background:radial-gradient(circle,#b9b98c,#6f8350 60%,transparent 70%)" role="img" aria-label="Cannabis bud"></div><div class="new"><b>NEW</b></div><div class="stars">★★★★★</div><div class="name">Mango Dusk</div><div class="price">$27.00 &nbsp;|&nbsp; $180.00</div></div>
<div class="abs card" style="left:349px;top:2456px"><div class="ph" style="background:radial-gradient(circle,#c2c29a,#7a8a5a 60%,transparent 70%)" role="img" aria-label="Cannabis bud"></div><div class="new"><b>NEW</b></div><div class="stars">★★★★★</div><div class="name">Mango Dusk</div><div class="price">$27.00 &nbsp;|&nbsp; $180.00</div></div>
<div class="abs card" style="left:610px;top:2456px;height:375px;border-color:#bfe3b4"><div class="ph" style="left:80px;width:80px;border-radius:10px;background:linear-gradient(#333 0 25%,#e2b530 25%)" role="img" aria-label="CBD oil bottle"></div><div class="new"><b>NEW</b></div><div class="stars">★★★★★</div><div class="name">Mango Dusk</div><div class="price">$27.00 &nbsp;|&nbsp; $180.00</div><div style="position:absolute;left:72px;top:320px;width:140px;height:50px;border-radius:50%;background:radial-gradient(closest-side,#7aa84a,rgba(122,168,74,0))" role="img" aria-label="Cannabis leaves"></div></div>
<div class="abs card" style="left:870px;top:2456px"><div class="ph" style="background:radial-gradient(circle,#b5a86a,#6b7a40 60%,transparent 70%)" role="img" aria-label="Cannabis bud"></div><div class="new"><b>NEW</b></div><div class="stars">★★★★★</div><div class="name">Mango Dusk</div><div class="price">$27.00 &nbsp;|&nbsp; $180.00</div></div>

<!-- Benefits -->
<div class="abs benefits" role="img" aria-label="Dark background with faint cannabis leaves"></div>
<svg class="abs leaf" style="left:580px;top:3010px" viewBox="0 0 40 56"><path d="M20 2 C24 14 24 26 20 40 C16 26 16 14 20 2Z M20 40 C10 34 4 26 2 18 C10 22 16 30 20 40Z M20 40 C30 34 36 26 38 18 C30 22 24 30 20 40Z" fill="var(--green)"/><line x1="20" y1="40" x2="20" y2="54" stroke="var(--green)" stroke-width="2"/></svg>
<div class="abs heading" style="top:3080px;color:#fff">Our Benefits</div>
<div class="abs plant" role="img" aria-label="Cannabis plant with buds"></div>

<div class="abs ben l" style="left:50px;top:3160px"><h4>Free Express Shipping</h4><p>Lorem ipsum dolor sit amet, consectetur ad do<br>eiusmod tempor incididunt ut labore et dolore magna</p></div>
<div class="abs ben l" style="left:50px;top:3262px"><h4>Highest Quality</h4><p>Lorem ipsum dolor sit amet, consectetur ad do<br>eiusmod tempor incididunt ut labore et dolore magna</p></div>
<div class="abs ben l" style="left:50px;top:3364px"><h4>100% Privacy</h4><p>Lorem ipsum dolor sit amet, consectetur ad do<br>eiusmod tempor incididunt ut labore et dolore magna</p></div>
<svg class="abs ico" style="left:388px;top:3160px" viewBox="0 0 46 46"><rect x="3" y="12" width="26" height="18" fill="none" stroke="#fff" stroke-width="2"/><path d="M29 17h9l5 7v6H29z" fill="none" stroke="#fff" stroke-width="2"/><circle cx="12" cy="33" r="4" fill="none" stroke="#fff" stroke-width="2"/><circle cx="36" cy="33" r="4" fill="none" stroke="#fff" stroke-width="2"/></svg>
<svg class="abs ico" style="left:388px;top:3262px" viewBox="0 0 46 46"><rect x="4" y="6" width="38" height="30" fill="none" stroke="#fff" stroke-width="2"/><circle cx="28" cy="28" r="8" fill="none" stroke="#fff" stroke-width="2"/></svg>
<svg class="abs ico" style="left:388px;top:3364px" viewBox="0 0 46 46"><path d="M23 40 C12 32 6 22 8 8 C16 14 20 24 23 40Z M23 40 C34 32 40 22 38 8 C30 14 26 24 23 40Z" fill="none" stroke="#fff" stroke-width="2"/></svg>

<div class="abs ben" style="left:834px;top:3160px"><h4>Best Price Guarantee</h4><p>Lorem ipsum dolor sit amet, consectetur ad do<br>eiusmod tempor incididunt ut labore et dolore magna</p></div>
<div class="abs ben" style="left:834px;top:3262px"><h4>Largest Variety</h4><p>Lorem ipsum dolor sit amet, consectetur ad do<br>eiusmod tempor incididunt ut labore et dolore magna</p></div>
<div class="abs ben" style="left:834px;top:3364px"><h4>100% Insured</h4><p>Lorem ipsum dolor sit amet, consectetur ad do<br>eiusmod tempor incididunt ut labore et dolore magna</p></div>
<svg class="abs ico" style="left:780px;top:3160px" viewBox="0 0 46 46"><circle cx="23" cy="23" r="17" fill="none" stroke="#fff" stroke-width="2"/><circle cx="23" cy="23" r="9" fill="none" stroke="#fff" stroke-width="2"/></svg>
<svg class="abs ico" style="left:780px;top:3262px" viewBox="0 0 46 46"><path d="M8 34 L20 14 L28 26 L34 18 L40 34Z" fill="none" stroke="#fff" stroke-width="2"/></svg>
<svg class="abs ico" style="left:780px;top:3364px" viewBox="0 0 46 46"><path d="M23 6 L38 12 V22 C38 32 31 38 23 41 C15 38 8 32 8 22 V12Z" fill="none" stroke="#fff" stroke-width="2"/></svg>

<!-- Blog -->
<svg class="abs leaf" style="left:580px;top:3598px" viewBox="0 0 40 56"><path d="M20 2 C24 14 24 26 20 40 C16 26 16 14 20 2Z M20 40 C10 34 4 26 2 18 C10 22 16 30 20 40Z M20 40 C30 34 36 26 38 18 C30 22 24 30 20 40Z" fill="var(--green)"/><line x1="20" y1="40" x2="20" y2="54" stroke="var(--green)" stroke-width="2"/></svg>
<div class="abs heading" style="top:3670px"><span>Latest</span> Blog</div>
<div class="abs post" style="left:100px"><div class="ph" style="background:linear-gradient(135deg,#d9d4cc,#6b6a5a 50%,#3b3a30)" role="img" aria-label="Hands preparing cannabis on a table"></div><h5>Lorem ipsum dolor sit amctetur adipiscing elit, sed do eiusmod tempor</h5><p>Lorem ipsum dolor sit amet, consectetur adipiing elit, sed do eiusmod tempor incididunt ut labore et dolore magna aliqua. Quis ipsum suspendisse</p><a>READ MORE ⟶</a></div>
<div class="abs post" style="left:438px"><div class="ph" style="background:linear-gradient(135deg,#e8e4dc,#8a6a4a 50%,#4a8a3a)" role="img" aria-label="Cannabis cookies with leaves"></div><h5>Lorem ipsum dolor sit amctetur adipiscing elit, sed do eiusmod tempor</h5><p>Lorem ipsum dolor sit amet, consectetur adipiing elit, sed do eiusmod tempor incididunt ut labore et dolore magna aliqua. Quis ipsum suspendisse</p><a>READ MORE ⟶</a></div>
<div class="abs post" style="left:775px"><div class="ph" style="background:linear-gradient(135deg,#2a6a7a,#4a9aaa 50%,#c89a7a)" role="img" aria-label="Person lighting a joint"></div><h5>Lorem ipsum dolor sit amctetur adipiscing elit, sed do eiusmod tempor</h5><p>Lorem ipsum dolor sit amet, consectetur adipiing elit, sed do eiusmod tempor incididunt ut labore et dolore magna aliqua. Quis ipsum suspendisse</p><a>READ MORE ⟶</a></div>

<!-- Testimonials -->
<div class="abs testi"></div>
<svg class="abs leaf" style="left:580px;top:4252px" viewBox="0 0 40 56"><path d="M20 2 C24 14 24 26 20 40 C16 26 16 14 20 2Z M20 40 C10 34 4 26 2 18 C10 22 16 30 20 40Z M20 40 C30 34 36 26 38 18 C30 22 24 30 20 40Z" fill="var(--green)"/><line x1="20" y1="40" x2="20" y2="54" stroke="var(--green)" stroke-width="2"/></svg>
<div class="abs heading" style="top:4320px"><span>Client</span> Testimonials</div>
<svg class="abs" style="left:84px;top:4476px" width="16" height="30" viewBox="0 0 16 30"><path d="M14 2 L2 15 L14 28" fill="none" stroke="#333" stroke-width="2"/></svg>
<svg class="abs" style="left:1098px;top:4476px" width="16" height="30" viewBox="0 0 16 30"><path d="M2 2 L14 15 L2 28" fill="none" stroke="#333" stroke-width="2"/></svg>
<div class="abs tcard" style="left:155px"><div class="abs quote">“</div><p>Lorem ipsum dolor sit amet, consectetur adipiscing elit, sed do eiusmod tempor incididunt ut lab magna aliqua. Quis ipsum suspendisse ultrices gravida. Rus commodo viverra maecenas accumsan</p><b>- JOHN DOE</b></div>
<div class="abs tcard" style="left:644px"><div class="abs quote">“</div><p>Lorem ipsum dolor sit amet, consectetur adipiscing elit, sed do eiusmod tempor incididunt ut lab magna aliqua. Quis ipsum suspendisse ultrices gravida. Rus commodo viverra maecenas accumsan</p><b>- JOHN DOE</b></div>
<div class="abs dot" style="left:564px;background:var(--green)"></div>
<div class="abs dot" style="left:579px"></div>
<div class="abs dot" style="left:594px"></div>
<div class="abs dot" style="left:609px"></div>
<div class="abs dot" style="left:624px"></div>

<!-- Newsletter -->
<div class="abs news">
  <svg class="abs" style="left:102px;top:22px" width="62" height="62" viewBox="0 0 62 62"><circle cx="31" cy="31" r="29" fill="none" stroke="#fff" stroke-width="2"/><rect x="18" y="22" width="26" height="18" fill="none" stroke="#fff" stroke-width="2"/><path d="M18 22 L31 33 L44 22" fill="none" stroke="#fff" stroke-width="2"/></svg>
  <div class="abs txt">Sign up today to receive exclusive updates<br>on the latest deals we have to offer. must be 18+</div>
  <input type="email" placeholder="Enter your email here">
  <div class="btn">Subscribe</div>
</div>

<!-- Footer -->
<div class="abs footer">
  <div class="abs fcol" style="left:103px;top:56px"><h6>Quick <span>Links</span></h6>
    <div style="display:flex;gap:34px"><ul><li>Home</li><li>Cannabis</li><li>Concentrates</li><li>Shop</li></ul><ul><li>About</li><li>How To Order</li><li>Faq's</li><li>Contact</li></ul></div></div>
  <div class="abs fcol" style="left:377px;top:56px"><h6>My <span>Account</span></h6><ul><li>My Account</li><li>Order History</li><li>My Favourites</li><li>Shipping &amp; Return</li></ul></div>
  <div class="abs fcol" style="left:600px;top:56px"><h6>Contact <span>Detail</span></h6><ul><li>1234 Somestreet Anywhere</li><li>USA 21212</li><li>☎ 888 888 8888</li><li>✉ info@lumivo.com</li></ul></div>
  <div class="abs brand" style="left:920px;top:70px"><i></i>LUMIVO</div>
  <div class="abs soc" style="left:938px;top:130px"></div>
  <div class="abs soc" style="left:980px;top:130px"></div>
  <div class="abs soc" style="left:1022px;top:130px"></div>
  <div class="abs" style="left:100px;top:200px;width:1000px;height:1px;background:#3a3150"></div>
</div>
<div class="abs copy">© 2020 LUMIVO. All Rights Reserved.</div>

</body>
</html>
```